13 Varno - new website design project

Our company Varno Electrical is developing a new lead generation website focused on Electrical, LED Lighting and Solar Power. We need a high converting website.

Example of our current website is www.varnoelectrical-example.com.au You can take content from this website for this new design. Our colours are red, black and white. For our new website we would like to promote Varno, Spark Every Day. Please listen to the jingle.

The below link is the company jingle that we have developed.
http://www.tunecraftdemo.com.au/vrn-tc-v1/

The key for this brief is to generate leads for Electrical, LED Lighting (for commercial) and Solar Power & Storage.

Target Market(s)

Business owners in Melbourne Victoria

Number of Pages Required

4 page

Colors
ec1f27
ffffff

Requirements
Must have
• This page must be clean, be in line with company branding and a high converting lead website.

```html
<!DOCTYPE html>
<html lang="en">
<head>
<meta charset="utf-8">
<title>Varno Electrical – Home</title>
<link href="https://fonts.googleapis.com/css2?family=Raleway:wght@400;500;600;700&family=Open+Sans:wght@400;600;700&family=Oswald:wght@600;700&display=swap" rel="stylesheet">
<style>
:root{
  --red:#ec1f27;
  --ink:#2b2b2f;
  --dark:#2d2d33;
  --text:#555;
  --muted:#888;
  --light:#f4f4f4;
  --panel:#efefef;
  --line:#dcdcdc;
  --white:#fff;
}
*{box-sizing:border-box;margin:0;padding:0}
html,body{width:1200px;height:2535px;overflow:hidden}
body{font-family:"Open Sans",Arial,sans-serif;color:var(--text);background:var(--white);font-size:12px}
.wrap{width:940px;margin:0 auto;position:relative;height:100%}
section,header,footer{position:relative;width:1200px;overflow:hidden}
h2{font-family:"Raleway",Arial,sans-serif;font-weight:600;color:var(--ink);font-size:27px;text-align:center;letter-spacing:.5px}
.lead{font-size:11px;color:var(--muted);text-align:center;line-height:18px;width:680px;margin:12px auto 0}
.btn-outline{display:inline-flex;align-items:center;gap:8px;border:2px solid var(--red);color:var(--red);font-family:"Raleway",sans-serif;font-weight:700;font-size:10px;padding:0 14px;height:34px;border-radius:3px;text-transform:uppercase}
.btn-solid{display:inline-flex;align-items:center;gap:10px;background:var(--red);color:var(--white);font-family:"Raleway",sans-serif;font-weight:700;font-size:11px;padding:0 20px;height:40px;border-radius:3px;text-transform:uppercase}
.btn-solid.small{height:34px;font-size:10px;padding:0 14px}
.chev{font-weight:700;font-size:13px}

/* header */
.site-header{height:135px;background:var(--white)}
.brand{position:absolute;left:0;top:24px}
.brand-name{display:flex;align-items:center;gap:8px;font-family:"Raleway",sans-serif;font-weight:700;font-size:40px;color:var(--ink);letter-spacing:-1px;line-height:1}
.brand-dot{width:20px;height:20px;border-radius:50%;background:var(--red)}
.brand-tag{font-family:"Raleway",sans-serif;font-weight:600;font-size:14px;color:var(--ink);margin-top:6px}
.brand-tag b{color:var(--red);font-weight:600}
.main-nav{position:absolute;left:280px;top:46px;display:flex;align-items:center}
.main-nav a{font-family:"Raleway",sans-serif;font-weight:700;font-size:11px;color:var(--ink);text-transform:uppercase;padding:0 26px;height:40px;display:flex;align-items:center}
.main-nav a.active{border:2px solid var(--red);color:var(--red);border-radius:3px;padding:0 28px;margin-right:14px}
.call{position:absolute;right:0;top:46px;display:flex;align-items:center;gap:12px;font-family:"Raleway",sans-serif;font-size:11px;font-weight:600;color:var(--ink)}
.call-icon{width:38px;height:38px;border-radius:50%;border:1.5px solid #bbb;display:flex;align-items:center;justify-content:center}
.call strong{color:var(--red);font-size:19px;font-weight:700;margin-left:2px}

/* hero */
.hero{height:507px;background:linear-gradient(100deg,#c9a48c 0%,#8a6a58 22%,#5b4b45 45%,#3a3634 70%,#6b4b3c 100%)}
.hero-photo{position:absolute;inset:0}
.hero-copy{position:absolute;left:676px;top:148px;color:var(--white)}
.hero-title{font-family:"Oswald",sans-serif;font-weight:700;font-style:italic;font-size:56px;letter-spacing:.5px;line-height:1}
.hero-text{font-family:"Raleway",sans-serif;font-size:20px;line-height:34px;margin:14px 0 20px;font-weight:500}
.slide-arrow{position:absolute;top:365px;width:46px;height:46px;border-radius:50%;background:rgba(40,40,40,.7);display:flex;align-items:center;justify-content:center}
.slide-arrow.prev{left:54px}.slide-arrow.next{right:54px}

/* features */
.features{height:583px;background:var(--light);padding-top:74px}
.feature-row{display:flex;justify-content:space-between;margin-top:42px}
.feature{width:300px;text-align:center}
.feature-pic{width:176px;height:176px;border-radius:50%;margin:0 auto;border:8px solid var(--white);box-shadow:0 0 0 1px #e2e2e2}
.pic-electrical{background:radial-gradient(circle at 65% 55%,#c8d64a 0,#7c8f5a 30%,#b8c2cc 60%,#e6e9ec 100%)}
.pic-led{background:linear-gradient(180deg,#2d5fb0 0%,#4d86d6 45%,#c6b36a 70%,#6a6a7a 100%)}
.pic-solar{background:linear-gradient(180deg,#3a7ed8 0%,#3a5e9e 45%,#c0542e 75%,#4f8a3a 100%)}
.feature h3{font-family:"Raleway",sans-serif;font-weight:700;font-size:12px;color:var(--ink);margin:22px 0 12px;text-transform:uppercase}
.feature p{font-size:10.5px;line-height:20px;color:var(--muted)}
.feature .btn-outline{margin-top:16px}

/* about */
.about{height:254px;background:linear-gradient(90deg,#1c2430 0%,#2b3340 40%,#1e252f 70%,#2a2424 100%);text-align:center;padding-top:52px}
.about-bg{position:absolute;inset:0}
.about .inner{position:relative}
.about h2{color:var(--white)}
.about p{color:#e8e8e8;font-size:11px;line-height:24px;width:820px;margin:14px auto 20px}

/* why */
.why{height:448px;background:var(--white);padding-top:46px}
.why-grid{display:flex;gap:2px;margin-top:44px}
.why-card{width:186.4px;height:224px;background:var(--panel);position:relative;text-align:center}
.why-card h4{height:46px;display:flex;align-items:center;justify-content:center;padding:0 10px}
.why-title{display:block;font-family:"Raleway",sans-serif;font-weight:700;font-size:10.5px;color:var(--ink);text-transform:uppercase;line-height:18px;text-align:center}
.why-title b{font-size:14px}
.why-icon{height:56px;display:flex;align-items:center;justify-content:center;margin-top:6px}
.why-card p{font-size:10px;line-height:18px;padding:6px 12px 0;color:var(--text)}
.why-more{position:absolute;left:0;right:0;bottom:0;height:36px;background:#c9c9c9;color:#e9e9e9;font-family:"Raleway",sans-serif;font-size:8.5px;font-weight:700;display:flex;align-items:center;justify-content:center;gap:6px;text-transform:uppercase}
.why-card.is-active{background:var(--dark)}
.why-card.is-active .why-title,.why-card.is-active p{color:var(--white)}
.why-card.is-active .why-more{background:var(--red);color:var(--white)}

/* clients */
.clients{height:368px;background:var(--light);padding-top:60px}
.clients-head{display:flex;justify-content:space-between;align-items:center}
.clients h3{font-family:"Raleway",sans-serif;font-weight:700;font-size:18px;color:var(--ink);letter-spacing:.3px}
.mini-arrows{display:flex;gap:10px;color:#999;font-size:14px;font-weight:700}
.clients-body{display:flex;margin-top:20px}
.client-card{width:287px;height:190px;background:var(--white);flex:none}
.client-name{height:68px;display:flex;align-items:center;justify-content:center;font-family:"Raleway",sans-serif;font-weight:700;font-size:30px;color:var(--red)}
.client-photo{height:122px;background:linear-gradient(180deg,#6a5a6e 0%,#a89aa6 40%,#7c6266 75%,#3a3032 100%)}
.testimonial{width:200px;flex:none;margin-left:30px;padding-top:4px}
.testimonial q{display:block;font-style:italic;font-size:11px;line-height:25px;color:var(--ink);quotes:"\201C" "\201D"}
.testimonial q::before{color:#aaa;font-size:20px;margin-right:6px;font-style:normal}
.testimonial q::after{color:#aaa;font-size:20px;margin-left:4px;font-style:normal}
.testimonial .who{color:var(--red);font-size:12px;margin-top:6px}
.testimonial .where{font-size:12px;color:var(--text);margin-top:8px}
.divider{width:1px;background:var(--line);height:205px;margin:0 26px 0 26px;flex:none}
.logo-grid{display:grid;grid-template-columns:184px 184px;gap:14px 14px}
.logo-tile{height:88px;background:var(--white);border:1px solid #e2e2e2;display:flex;align-items:center;justify-content:center;font-family:"Raleway",sans-serif;font-weight:700;font-size:17px;color:var(--ink);text-align:center;line-height:1.2}
.logo-tile.red{color:var(--red)}

/* footer */
.site-footer{height:240px;background:var(--white)}
.foot-cols{display:flex;padding-top:48px}
.foot-brand{width:255px}
.foot-brand .brand-name{font-size:36px}
.foot-brand .brand-tag{font-size:13px;margin-top:4px}
.socials{display:flex;gap:8px;margin:20px 0 10px 30px}
.socials span{width:24px;height:24px;border-radius:50%;background:var(--ink)}
.copy{font-size:10px;color:var(--text)}
.foot-col{border-left:1px solid #ececec;padding-left:26px;height:172px}
.foot-col h5{font-family:"Raleway",sans-serif;font-weight:700;font-size:12px;color:var(--ink);text-transform:uppercase;margin-bottom:18px}
.foot-nav{width:190px}
.foot-nav li{list-style:none;font-size:9.5px;color:var(--text);text-transform:uppercase;margin-bottom:13px}
.foot-nav li::before{content:"▸";font-size:9px;margin-right:6px;color:#555}
.foot-contact{width:285px}
.foot-contact li{list-style:none;display:flex;gap:10px;font-size:10.5px;line-height:20px;color:var(--text);margin-bottom:8px}
.foot-contact li b{font-weight:400;font-size:13px;color:var(--ink)}
.foot-news{width:210px}
.news-input{width:205px;height:36px;border:1px solid #e2e2e2;font-size:9.5px;color:#999;display:flex;align-items:center;padding-left:12px}
.news-btn{margin-top:12px;width:94px;height:36px;border:2px solid var(--red);border-radius:3px;color:var(--red);font-family:"Raleway",sans-serif;font-weight:700;font-size:10px;display:flex;align-items:center;justify-content:center}
</style>
</head>
<body>

<header class="site-header">
  <div class="wrap">
    <div class="brand">
      <div class="brand-name"><span class="brand-dot"></span>VARNO</div>
      <div class="brand-tag">Spark <b>Every</b> Day</div>
    </div>
    <nav class="main-nav">
      <a class="active">Home</a>
      <a>Varno Story</a>
      <a>Our Work</a>
      <a>Contact Us</a>
    </nav>
    <div class="call">
      <span class="call-icon">
        <svg width="16" height="16" viewBox="0 0 24 24"><path fill="#ec1f27" d="M6.6 10.8a15.2 15.2 0 0 0 6.6 6.6l2.2-2.2c.3-.3.7-.4 1-.2 1.1.4 2.3.6 3.6.6.6 0 1 .4 1 1V20c0 .6-.4 1-1 1A17 17 0 0 1 3 4c0-.6.4-1 1-1h3.5c.6 0 1 .4 1 1 0 1.3.2 2.5.6 3.6.1.3 0 .7-.2 1z"/></svg>
      </span>
      VARNO : <strong>13 7710</strong>
    </div>
  </div>
</header>

<section class="hero">
  <div class="hero-photo" role="img" aria-label="Electrician testing a switchboard with a red probe"></div>
  <div class="hero-copy">
    <div class="hero-title">VARNO ELECTRICAL</div>
    <p class="hero-text">Developing a new lead generation website<br>focused on Electrical, LED Lighting...</p>
    <span class="btn-solid">View morer information <span class="chev">›</span></span>
  </div>
  <span class="slide-arrow prev"><svg width="12" height="14" viewBox="0 0 12 14"><path d="M9 1 3 7l6 6" stroke="#ddd" stroke-width="2.5" fill="none"/></svg></span>
  <span class="slide-arrow next"><svg width="12" height="14" viewBox="0 0 12 14"><path d="m3 1 6 6-6 6" stroke="#ddd" stroke-width="2.5" fill="none"/></svg></span>
</section>

<section class="features">
  <div class="wrap">
    <h2>FEATURES</h2>
    <p class="lead">Accusantium doloremque laudantium, totam rem aperiam, eaque ipsa quae ab illo inventore veritatis et quasi architecto beatae vitae dicta sunt explicabo. Nemo enim ipsam voluptatem quia</p>
    <div class="feature-row">
      <div class="feature">
        <div class="feature-pic pic-electrical" role="img" aria-label="Electrician in hard hat working on a switchboard"></div>
        <h3>Electrical</h3>
        <p>Upgrading your business to LED Lighting is one of the quick est ways to slash the operating costs of your business. Most businesses use a combination...</p>
        <span class="btn-outline">Read more <span class="chev">›</span></span>
      </div>
      <div class="feature">
        <div class="feature-pic pic-led" role="img" aria-label="Illuminated bridge at dusk"></div>
        <h3>LED Lighting</h3>
        <p>Upgrading your business to LED Lighting is one of the quick est ways to slash the operating costs of your business. Most businesses use a combination...</p>
        <span class="btn-outline">Read more <span class="chev">›</span></span>
      </div>
      <div class="feature">
        <div class="feature-pic pic-solar" role="img" aria-label="Solar panels on a tiled roof"></div>
        <h3>Solar Power</h3>
        <p>Upgrading your business to LED Lighting is one of the quick est ways to slash the operating costs of your business. Most businesses use a combination...</p>
        <span class="btn-outline">Read more <span class="chev">›</span></span>
      </div>
    </div>
  </div>
</section>

<section class="about">
  <div class="about-bg" role="img" aria-label="Dark close-up of electrical cabling"></div>
  <div class="wrap inner">
    <h2>ABOUTUS</h2>
    <p>Varno Electrical was formed to be an expert Electricity Contracting Company providing services to all Residential and Commercial Customers. With over 10 years of experience, Varno Electrical has developed a highly-experienced team of professionals that ensure all our customer expectations are met.</p>
    <span class="btn-solid small">Read more <span class="chev">›</span></span>
  </div>
</section>

<section class="why">
  <div class="wrap">
    <h2>WHY CHOOSE US?</h2>
    <p class="lead">Accusantium doloremque laudantium, totam rem aperiam, eaque ipsa quae ab illo inventore veritatis et quasi architecto beatae vitae dicta sunt explicabo. Nemo enim ipsam voluptatem quia</p>
    <div class="why-grid">
      <div class="why-card is-active">
        <h4><span class="why-title"><b>01.</b>Professional Service</span></h4>
        <div class="why-icon">
          <svg width="60" height="50" viewBox="0 0 60 50" fill="#fff">
            <circle cx="22" cy="28" r="13"/><circle cx="22" cy="28" r="5" fill="#2d2d33"/>
            <rect x="19" y="11" width="6" height="6"/><rect x="19" y="39" width="6" height="6"/><rect x="5" y="25" width="6" height="6"/><rect x="33" y="25" width="6" height="6"/>
            <circle cx="45" cy="14" r="8"/><circle cx="45" cy="14" r="3" fill="#2d2d33"/>
            <rect x="43" y="3" width="4" height="4"/><rect x="43" y="21" width="4" height="4"/><rect x="34" y="12" width="4" height="4"/><rect x="52" y="12" width="4" height="4"/>
          </svg>
        </div>
        <p>When you hire a Varno Electrical Electrician you will get...</p>
        <div class="why-more">Click here for more info <span>›</span></div>
      </div>
      <div class="why-card">
        <h4><span class="why-title"><b>02.</b>5 Year Workmanship Guarantee</span></h4>
        <div class="why-icon">
          <svg width="50" height="46" viewBox="0 0 50 46" fill="#2b2b2f">
            <rect x="4" y="20" width="10" height="24"/>
            <path d="M18 20 28 4c3 0 5 2 4 6l-2 8h14c3 0 4 3 3 5l-5 18c-1 2-2 3-4 3H18z"/>
          </svg>
        </div>
        <p>You can buy with confidence as all of our work has...</p>
        <div class="why-more">Click here for more info <span>›</span></div>
      </div>
      <div class="why-card">
        <h4><span class="why-title"><b>03.</b>Value for Money</span></h4>
        <div class="why-icon">
          <svg width="52" height="40" viewBox="0 0 52 40">
            <rect x="2" y="4" width="48" height="32" fill="#2b2b2f"/>
            <rect x="8" y="10" width="36" height="20" fill="#efefef"/>
            <circle cx="26" cy="20" r="8" fill="#2b2b2f"/>
            <text x="26" y="24" text-anchor="middle" font-family="Open Sans,sans-serif" font-size="11" font-weight="700" fill="#efefef">1</text>
          </svg>
        </div>
        <p>We provide extremelycompe titive pricing, which...</p>
        <div class="why-more">Click here for more info <span>›</span></div>
      </div>
      <div class="why-card">
        <h4><span class="why-title"><b>04.</b>Environmentally Friendly</span></h4>
        <div class="why-icon">
          <svg width="50" height="46" viewBox="0 0 50 46" fill="none" stroke="#2b2b2f" stroke-width="6" stroke-linejoin="round">
            <path d="M18 8 25 4l7 10"/><path d="M40 22l5 9-6 9H30"/><path d="M18 40H9l-5-9 5-9"/>
            <path d="M29 8l5 6-8 1" stroke-width="3" fill="#2b2b2f"/>
          </svg>
        </div>
        <p>We a committed to reducing carbon emissions by...</p>
        <div class="why-more">Click here for more info <span>›</span></div>
      </div>
      <div class="why-card">
        <h4><span class="why-title"><b>05.</b>Fully Insured</span></h4>
        <div class="why-icon">
          <svg width="50" height="46" viewBox="0 0 50 46">
            <path d="M3 20C5 8 15 2 25 2s20 6 22 18c-3-2-6-2-8 0-2-2-6-2-8 0-2-2-5-2-6 0-2-2-5-2-8 0-2-2-5-2-8 0z" fill="#2b2b2f"/>
            <path d="M25 18v20c0 5-7 5-7 0" stroke="#2b2b2f" stroke-width="3" fill="none"/>
          </svg>
        </div>
        <p>Varno Electrical is fully insured and equipped to...</p>
        <div class="why-more">Click here for more info <span>›</span></div>
      </div>
    </div>
  </div>
</section>

<section class="clients">
  <div class="wrap">
    <div class="clients-head">
      <h3>OUR SATISFIED CLIENTS INCLUDE</h3>
      <div class="mini-arrows"><span>‹</span><span>›</span></div>
    </div>
    <div class="clients-body">
      <div class="client-card">
        <div class="client-name">Brightmart</div>
        <div class="client-photo" role="img" aria-label="Interior of a retail store with lit display aisles"></div>
      </div>
      <div class="testimonial">
        <q>They clean up after the job, explained everything I needed to know and answered all questions, very professional. Will use them again in the future!</q>
        <div class="who">-R. Mercer</div>
        <div class="where">Northvale VIC</div>
      </div>
      <div class="divider"></div>
      <div class="logo-grid">
        <div class="logo-tile red">Brightmart</div>
        <div class="logo-tile">Ferrovale</div>
        <div class="logo-tile">Harlow Signs</div>
        <div class="logo-tile red">Heron Plumbing<br>Supplies</div>
      </div>
    </div>
  </div>
</section>

<footer class="site-footer">
  <div class="wrap">
    <div class="foot-cols">
      <div class="foot-brand">
        <div class="brand-name"><span class="brand-dot"></span>VARNO</div>
        <div class="brand-tag">Spark <b>Every</b> Day</div>
        <div class="socials"><span></span><span></span><span></span></div>
        <div class="copy">Copyrights © varnoelectrical.2017</div>
      </div>
      <div class="foot-col foot-nav">
        <h5>Navigation</h5>
        <ul><li>Home</li><li>Varno Story</li><li>Our Work</li><li>Contact Us</li></ul>
      </div>
      <div class="foot-col foot-contact">
        <h5>Contact Info</h5>
        <ul>
          <li><svg width="12" height="16" viewBox="0 0 12 16"><path d="M6 1a5 5 0 0 0-5 5c0 4 5 9 5 9s5-5 5-9a5 5 0 0 0-5-5z" fill="none" stroke="#ec1f27" stroke-width="1.5"/><circle cx="6" cy="6" r="1.8" fill="#ec1f27"/></svg><span>varnoelectrical,Company Name,<br>Street Name,City-454</span></li>
          <li><svg width="14" height="14" viewBox="0 0 24 24"><path fill="none" stroke="#ec1f27" stroke-width="2" d="M6.6 10.8a15.2 15.2 0 0 0 6.6 6.6l2.2-2.2c.3-.3.7-.4 1-.2 1.1.4 2.3.6 3.6.6.6 0 1 .4 1 1V20c0 .6-.4 1-1 1A17 17 0 0 1 3 4c0-.6.4-1 1-1h3.5c.6 0 1 .4 1 1 0 1.3.2 2.5.6 3.6.1.3 0 .7-.2 1z"/></svg><span>Phone : <b>137710</b></span></li>
          <li><svg width="14" height="12" viewBox="0 0 14 12"><rect x="1" y="1" width="12" height="10" fill="none" stroke="#ec1f27" stroke-width="1.4"/><path d="m1 1 6 5 6-5" fill="none" stroke="#ec1f27" stroke-width="1.4"/></svg><span>Email : info@varnoelectrical-example.com.au</span></li>
        </ul>
      </div>
      <div class="foot-col foot-news">
        <h5>Newsletter</h5>
        <div class="news-input">Enter Your E-mail Address</div>
        <div class="news-btn">SUBSCRIBE</div>
      </div>
    </div>
  </div>
</footer>

</body>
</html>
```